Foxglen Company Flyer - RV Solar and Residential Solar

We would like to create a tri-fold brochure for our company for distribution in the mail. This will advertise our services, products and some references.

Our cover page should include a logo and contact information as well as some solar stock imagery.

Our inside pages should cover residential solar, RV solar and a solar education / facts portion.

The rear pages would be left for our remaining services and some references / testimonials.

Target Market(s)

Residential Homeowners and Recreational Vehicles

Industry/Entity Type

Solar Energy

Font styles to use
Serif
Sans Serif

Requirements
Must have
• Must match the color scheme of our logo.
Nice to have
• Solar stock images for RV solar and residential solar.
Either a black or white background with our logo is eye-catching,

```html
<!DOCTYPE html>
<html lang="en">
<head>
<meta charset="utf-8">
<title>Foxglen Renewables – Tri-fold Brochure Outside</title>
<link rel="stylesheet" href="https://fonts.googleapis.com/css2?family=Raleway:ital,wght@0,400;0,500;0,700;0,800;1,400&family=Libre+Baskerville:wght@700&family=Oswald:wght@500&display=swap">
<style>
  :root{
    --blue:#33479c;
    --green:#5aac2c;
    --green-bright:#4fbf22;
    --cyan:#3bb4e0;
    --white:#ffffff;
    --ink:#2c2c2c;
    --stage:#3b3b3b;
    --dash:#d6336c;
  }
  *{margin:0;padding:0;box-sizing:border-box}
  html,body{width:828px;height:1200px;overflow:hidden}
  body{background:var(--stage);font-family:"Raleway",Arial,sans-serif;color:var(--ink)}
  .brochure{position:absolute;left:14px;top:315px;width:800px;height:570px;overflow:hidden;background:var(--white)}
  .brochure-art{position:absolute;inset:0;width:800px;height:570px}
  .abs{position:absolute}

  /* Left panel */
  .facts-mark{left:20px;top:24px;width:14px;height:14px;border-radius:50%;background:var(--cyan)}
  .facts-title{left:53px;top:20px;font-weight:800;font-size:13px;line-height:15px}
  .facts-title .kicker{color:var(--green)}
  .facts-title .main{color:var(--blue)}
  .facts-rule{left:53px;top:51px;width:70px;height:1.5px;background:var(--blue)}
  .facts-list{left:22px;top:63px;width:234px;list-style:none;font-size:7.4px;line-height:9.6px}
  .facts-list li{position:relative;padding-left:13px;margin-bottom:3.6px;text-align:justify}
  .facts-list li::before{content:"";position:absolute;left:1px;top:3px;width:3.5px;height:3.5px;border-radius:50%;background:var(--blue)}
  .relocate{left:0;top:459px;width:271px;text-align:center}
  .relocate h3{color:var(--green-bright);font-weight:800;font-size:12.5px;line-height:14.5px}
  .relocate p{color:var(--white);font-size:12.5px;line-height:15.5px;margin-top:5px}

  /* Middle panel */
  .project{left:300px;top:18px;width:196px;text-align:center}
  .project h2{font-weight:800;font-size:15.5px;line-height:19px}
  .project h2 .g{color:var(--green)}
  .project h2 .b{color:var(--blue)}
  .project .rule{width:52px;height:1.5px;background:var(--blue);margin:8px auto 0}
  .project h4{color:var(--green);font-weight:800;font-size:9.6px;margin-top:10px}
  .project p{font-size:9.6px;line-height:13px;margin-top:1px}
  .quote-box{left:307px;top:208px;width:195px;height:92px;border:1px dashed var(--dash);border-radius:8px}
  .quote-mark{left:373px;top:192px;width:54px;height:30px;text-align:center;color:var(--green);font-family:"Libre Baskerville",Georgia,serif;font-size:46px;line-height:46px;background:var(--white);overflow:hidden}
  .quote-text{left:312px;top:222px;width:185px;text-align:center;font-style:italic;font-size:6.6px;line-height:10.3px}
  .client{left:307px;top:291px;width:195px;text-align:center;color:var(--blue);font-weight:700;font-size:10.5px;line-height:18px}
  .client span{background:var(--white);padding:0 14px}
  .touch{left:286px;top:451px;font-weight:700;font-size:13px;color:var(--white)}
  .touch .g{color:var(--green-bright)}
  .touch-icons{left:289px;top:473px;display:flex;gap:6px}
  .touch-icons svg{width:13px;height:13px}
  .touch-lines{left:289px;top:491px;color:var(--white);font-size:7.2px;line-height:10.8px}
  .follow{left:448px;top:502px;color:var(--white);font-size:7px}
  .social{left:443px;top:518px;display:flex;gap:8px}
  .social i{display:block;width:13px;height:13px;border-radius:50%;background:var(--white)}
  .strip-text{top:553px;color:var(--white);font-size:8.4px;letter-spacing:1px}
  .strip-left{left:0;width:271px;text-align:center}
  .strip-mid{left:271px;width:265px;text-align:center}

  /* Right panel */
  .brand{left:544px;top:30px;width:258px;text-align:center}
  .brand .mark{width:46px;height:46px;border-radius:50%;background:var(--cyan);margin:0 auto 10px}
  .brand .name{color:var(--blue);font-weight:800;font-size:26px;line-height:28px;letter-spacing:.5px}
  .brand .sub{color:var(--blue);font-weight:800;font-size:12px;letter-spacing:1px;border-top:1px solid var(--blue);display:inline-block;padding-top:2px;margin-top:2px}
  .badge{left:707px;top:355px;width:88px;text-align:center;font-family:"Oswald",Arial,sans-serif;color:var(--green);font-size:12.5px;line-height:12.5px}
  .badge .tag{display:inline-block;margin-top:2px;background:#222;color:var(--white);font-size:8px;line-height:10px;padding:0 6px}
  .welcome{left:536px;top:442px;width:264px;text-align:center}
  .welcome .pre{color:var(--green-bright);font-size:11.5px;letter-spacing:4px}
  .welcome h1{font-family:"Libre Baskerville",Georgia,serif;color:var(--white);font-size:23px;line-height:29px;margin-top:2px}
  .quote-pill{left:610px;top:527px;width:162px;height:20px;border-radius:10px 10px 0 0;background:var(--white);color:var(--blue);font-weight:800;font-size:12px;line-height:21px;text-align:center}
  .phones{left:536px;top:549px;width:264px;text-align:center;color:var(--white);font-weight:800;font-size:12.6px}
  .phones .or{font-weight:400}
</style>
</head>
<body>
<main class="brochure">
  <svg class="brochure-art" viewBox="0 0 800 570" xmlns="http://www.w3.org/2000/svg">
    <defs>
      <linearGradient id="skyPanels" x1="0" y1="0" x2="0" y2="1">
        <stop offset="0" stop-color="#e4edf5"/>
        <stop offset=".45" stop-color="#c9d6e4"/>
        <stop offset=".65" stop-color="#6d7d97"/>
        <stop offset=".85" stop-color="#4b4a3a"/>
        <stop offset="1" stop-color="#3d4a2a"/>
      </linearGradient>
      <radialGradient id="bulb" cx=".5" cy=".45" r=".6">
        <stop offset="0" stop-color="#e9ef5a"/>
        <stop offset=".5" stop-color="#7fb235"/>
        <stop offset="1" stop-color="#2f5a1d"/>
      </radialGradient>
      <linearGradient id="house" x1="0" y1="0" x2="0" y2="1">
        <stop offset="0" stop-color="#1f5d52"/>
        <stop offset=".6" stop-color="#8fb9b4"/>
        <stop offset="1" stop-color="#4d8a33"/>
      </linearGradient>
    </defs>
    <rect width="800" height="570" fill="#ffffff"/>
    <g role="img" aria-label="Photo of a solar panel array in a field under a bright sky">
      <path d="M510,0 H800 V445 C700,420 600,410 472,420 C525,300 530,150 510,0 Z" fill="url(#skyPanels)"/>
    </g>
    <path d="M508,0 C528,150 523,300 470,422" fill="none" stroke="#5aac2c" stroke-width="9"/>
    <path d="M0,366 C80,344 160,340 230,356 C300,374 360,416 420,416 C480,416 520,398 560,393 C640,383 720,410 800,428" fill="none" stroke="#5aac2c" stroke-width="4"/>
    <path d="M0,372 C80,350 160,346 230,362 C300,380 360,422 420,422 C480,422 520,404 560,399 C640,389 720,416 800,434 V547 H0 Z" fill="#33479c"/>
    <rect x="0" y="547" width="271" height="23" fill="#5aac2c"/>
    <rect x="271" y="547" width="265" height="23" fill="#3bb4e0"/>
    <rect x="536" y="547" width="264" height="23" fill="#5aac2c"/>
    <circle cx="136" cy="358" r="86" fill="#4fbf22"/>
    <circle cx="136" cy="358" r="78" fill="url(#bulb)" role="img" aria-label="Photo of a glowing light bulb with a globe inside, resting in green leaves"/>
    <circle cx="344" cy="381" r="58" fill="#4fbf22"/>
    <circle cx="344" cy="381" r="51" fill="url(#house)" role="img" aria-label="Illustration of a wireframe house rising from a tablet over a grassy field"/>
    <rect x="750" y="370" width="50" height="44" fill="#3bb4e0"/>
    <circle cx="750" cy="394" r="46" fill="#3bb4e0"/>
    <circle cx="750" cy="394" r="41" fill="#ffffff"/>
  </svg>

  <!-- Left panel -->
  <span class="abs facts-mark"></span>
  <div class="abs facts-title"><div class="kicker">SOLAR 101</div><div class="main">SOME FACTS ON SOLAR</div></div>
  <span class="abs facts-rule"></span>
  <ul class="abs facts-list">
    <li>Alberta is the sunniest province in Canada and comparable to Florida</li>
    <li>Systems are designed to last 25 years but operate for as long as 40 years</li>
    <li>Virtually no maintenance required!</li>
    <li>How your power bill works.</li>
    <li>Protect yourself from rising power costs</li>
    <li>Not everyone can have solar. Once 30-40% of the market has solar, utilities will not allow all solar systems to be installed.</li>
    <li>Dispel the snow myth: Snow only reduces a systems output by 5-8% over the course of a year. This is because our sunny hours are mostly made up in the longer summer days.</li>
    <li>Solar panels are nearly indestructible. Hail cannot damage a solar panel.</li>
    <li>Any extra power generated in the summer is sold back to the grid as a credit on your bill.</li>
  </ul>
  <div class="abs relocate">
    <h3>SELLING YOUR HOUSE AND<br>LOVE YOUR SOLAR?</h3>
    <p>We will relocate the system to<br>your new home for a small fee.</p>
  </div>
  <div class="abs strip-text strip-left">Sales@Foxglenrenewables.com</div>

  <!-- Middle panel -->
  <section class="abs project">
    <h2><span class="g">A GREAT PLACE TO<br>START YOUR</span><br><span class="b">RENEWABLE ENERGY<br>PROJECT!</span></h2>
    <div class="rule"></div>
    <h4>OTHER SERVICES OFFERED</h4>
    <p>Agricultural pivot power, oil and gas<br>systems, energy audits, battery<br>storage systems, off grid designs for<br>cottages / lake houses</p>
  </section>
  <div class="abs quote-box"></div>
  <div class="abs quote-mark">&ldquo;</div>
  <p class="abs quote-text">Lorem Ipsum is simply dummy text of the printing and typesetting industry. Lorem Ipsum has been the industry's standard dummy text ever since the 1500s, when an unknown printer took a galley of type and scrambled it to make a type specimen book.</p>
  <div class="abs client"><span>Client Name</span></div>
  <div class="abs touch"><span class="g">GET IN</span> TOUCH</div>
  <div class="abs touch-icons">
    <svg viewBox="0 0 14 14"><circle cx="7" cy="7" r="7" fill="#3bb4e0"/><path d="M7 3.2a2.6 2.6 0 0 0-2.6 2.6C4.4 7.8 7 10.8 7 10.8s2.6-3 2.6-5A2.6 2.6 0 0 0 7 3.2Z" fill="#fff"/><circle cx="7" cy="5.8" r="1" fill="#3bb4e0"/></svg>
    <svg viewBox="0 0 14 14"><circle cx="7" cy="7" r="7" fill="#3bb4e0"/><path d="M4.6 3.6l1.4 1.6-.7 1.1a5 5 0 0 0 2.4 2.4l1.1-.7 1.6 1.4-.8 1.1C6.9 10.4 3.6 7.1 3.5 4.4Z" fill="#fff"/></svg>
    <svg viewBox="0 0 14 14"><circle cx="7" cy="7" r="7" fill="#3bb4e0"/><rect x="3.6" y="4.6" width="6.8" height="4.8" fill="none" stroke="#fff" stroke-width=".9"/><path d="M3.6 4.6 7 7.4l3.4-2.8" fill="none" stroke="#fff" stroke-width=".9"/></svg>
  </div>
  <div class="abs touch-lines">Pine Hollow, Alberta, Canada<br>403.555.0187<br>780.555.0142<br>sales@foxglenrenewables.com</div>
  <div class="abs follow">Follow Us</div>
  <div class="abs social"><i></i><i></i><i></i></div>
  <div class="abs strip-text strip-mid">www.foxglenrenewables.com</div>

  <!-- Right panel (cover) -->
  <div class="abs brand">
    <div class="mark"></div>
    <div class="name">FOXGLEN</div>
    <div class="sub">RENEWABLES</div>
  </div>
  <div class="abs badge">LOWEST<br>INSTALLED<br>SOLAR PRICE<br><span class="tag">GUARANTEED</span></div>
  <div class="abs welcome">
    <div class="pre">WELCOME TO</div>
    <h1>FOXGLEN<br>RENEWABLES</h1>
  </div>
  <div class="abs quote-pill">Get a Free Quotation</div>
  <div class="abs phones">780-555-0142 <span class="or">or</span> 403-555-0187</div>
</main>
</body>
</html>
```